Founder / concept developer needs business card // Consultant needs VCARD

I need a business card for me as a founding consultant in Berlin. I advise entrepreneurs, especially in the design of business ideas, business plans or financing applications. More information about this in the annexes. My USP: I design / structure complex ideas and projects convincingly so that my client is successful. I want to communicate professionalism, effectiveness and clarity. Colors like from the range BLACK-GRAY-GREEN. I am 27 years old, I have studied business for 7 years. Attachments: - Business card design (only idea, do not focus on it) - Website screenshot (only idea, do not focus on it)

Target Market(s)

Target group: Founder (20-50 yrs, m / w, needy, in "break-up phase") and CONTRACTOR / "financier" (30-55 yrs, m / w, often public service "routine-oriented"). The foundations are in quite different industries: digital, craft, tourism, retail, services, etc. Almost all German.

Industry/Entity Type

Consultant

Contact Information for Business Card

Lukas Brennwald
M. Sc., International Business Administration
Gründungsberater, Konzeptentwickler
www.kelvoran-mitrel.de
Postfach-Zugang@kelvoran.de
Tel. 0481 294 3172

Colors

Designer to choose colors to be used in the design.

Requirements
Must have
• Professionalism, persuasiveness, clarity
Nice to have
• memorability
Should not have
• Schnörkelei

```html
<!DOCTYPE html>
<html lang="de">
<head>
<meta charset="utf-8">
<title>Lukas Brennwald – Visitenkarte</title>
<link rel="stylesheet" href="https://fonts.googleapis.com/css2?family=Montserrat:wght@400;500&family=Roboto:wght@400&display=swap">
<style>
  :root {
    --stage: #1c1c1c;
    --card: #151515;
    --card-edge: #262626;
    --ink: #f2f2f2;
    --ink-soft: #bdbdbd;
    --green: #5cb848;
    --green-dark: #2f5e26;
    --mesh: #3a3a3a;
  }
  * { box-sizing: border-box; margin: 0; padding: 0; }
  html, body { width: 1200px; height: 1200px; overflow: hidden; }
  body {
    background: var(--stage);
    display: flex;
    flex-direction: column;
    align-items: center;
    justify-content: center;
    gap: 40px;
    font-family: "Roboto", Arial, sans-serif;
  }
  .card {
    position: relative;
    width: 820px;
    height: 530px;
    background: var(--card);
    border: 1px solid var(--card-edge);
    box-shadow: 0 18px 40px rgba(0,0,0,0.55);
    overflow: hidden;
  }
  .network-graphic {
    position: absolute;
    left: 40px;
    right: 40px;
    border-radius: 50% 50% 0 0 / 100% 100% 0 0;
  }
  /* front */
  .card--front .network-graphic {
    top: 250px;
    height: 320px;
    background: radial-gradient(ellipse at 50% 30%, rgba(70,70,70,0.35), rgba(40,40,40,0.15) 60%, transparent 80%);
  }
  .brand {
    position: absolute;
    top: 150px;
    left: 0;
    right: 0;
    text-align: center;
  }
  .brand__mark {
    display: block;
    width: 118px;
    height: 70px;
    margin: 0 auto 18px;
    border: 3px solid var(--green);
  }
  .brand__name {
    font-family: "Montserrat", Arial, sans-serif;
    font-weight: 500;
    font-size: 30px;
    letter-spacing: 4px;
    text-transform: uppercase;
    color: var(--ink);
  }
  .brand__web {
    margin-top: 6px;
    font-size: 19px;
    letter-spacing: 1.5px;
    color: var(--green);
  }
  /* back */
  .card--back .network-graphic {
    top: 200px;
    height: 420px;
    background: radial-gradient(ellipse at 50% 25%, rgba(110,110,110,0.4), rgba(60,60,60,0.2) 55%, transparent 80%);
  }
  .person {
    position: absolute;
    top: 62px;
    left: 0;
    right: 0;
    text-align: center;
  }
  .person__name {
    font-family: "Montserrat", Arial, sans-serif;
    font-weight: 500;
    font-size: 27px;
    letter-spacing: 3.5px;
    text-transform: uppercase;
    color: var(--ink);
  }
  .person__role {
    margin-top: 6px;
    font-size: 19px;
    line-height: 1.3;
    color: var(--green);
  }
  .phone {
    position: absolute;
    left: 70px;
    bottom: 72px;
    font-size: 28px;
    letter-spacing: 1px;
    color: var(--ink);
  }
  .phone__label { color: var(--green); }
  .contact {
    position: absolute;
    right: 60px;
    bottom: 44px;
    list-style: none;
    text-align: right;
    font-size: 20px;
    line-height: 1.6;
    color: var(--ink);
  }
  .contact__item { display: flex; align-items: center; justify-content: flex-end; gap: 12px; }
  .contact__icon { width: 22px; height: 22px; flex: none; }
</style>
</head>
<body>

  <section class="card card--front">
    <div class="network-graphic" role="img" aria-label="Feines Netzwerk-Gitter in Form einer Weltkugel, sehr dunkel"></div>
    <div class="brand">
      <span class="brand__mark"></span>
      <div class="brand__name">Lukas Brennwald</div>
      <div class="brand__web">www.kelvoran-mitrel.de</div>
    </div>
  </section>

  <section class="card card--back">
    <div class="network-graphic" role="img" aria-label="Netzwerk-Gitter in Form einer Weltkugel mit grünen Knotenpunkten"></div>
    <div class="person">
      <div class="person__name">Lukas Brennwald</div>
      <p class="person__role">M. Sc., International Business Administration<br>Gründungsberater, Konzeptentwickler</p>
    </div>
    <p class="phone"><span class="phone__label">Tel:</span> 0481 294 3172</p>
    <ul class="contact">
      <li class="contact__item">Postfach-Zugang@kelvoran.de
        <svg class="contact__icon" viewBox="0 0 22 22" aria-hidden="true">
          <rect x="2" y="5" width="18" height="12" fill="var(--green)"/>
          <path d="M2 5 L11 12 L20 5" fill="none" stroke="var(--card)" stroke-width="1.6"/>
        </svg>
      </li>
      <li class="contact__item">www.kelvoran-mitrel.de
        <svg class="contact__icon" viewBox="0 0 22 22" aria-hidden="true">
          <circle cx="11" cy="11" r="9" fill="var(--green)"/>
          <ellipse cx="11" cy="11" rx="4" ry="9" fill="none" stroke="var(--card)" stroke-width="1.3"/>
          <line x1="2" y1="11" x2="20" y2="11" stroke="var(--card)" stroke-width="1.3"/>
        </svg>
      </li>
    </ul>
  </section>

</body>
</html>
```